Freight broker online presence/customer portal track shipping

I sleek design showing what we do, broker freight. What we specialize in, chemicals and any freight where domestic or international. We want a home page, a customer portal button on front page that lets clients check on status of their freight (integrate with our transportation management system. Contact page,
COMPANIES THAT HAVE PALLETS TO MOVE.
https://www.tallowmerelogistics.com/
https://www.quivendale.com/
https://www.rkpellow.com/
3 page

```html
<!DOCTYPE html>
<html lang="en">
<head>
<meta charset="utf-8">
<title>Freight Broker</title>
<link rel="stylesheet" href="https://fonts.googleapis.com/css2?family=Roboto:wght@400;500;700;900&display=swap">
<style>
:root{
  --blue:#2f74b8;
  --green:#8dc63f;
  --teal:#2fb7a0;
  --ink:#1d1d1d;
  --muted:#777;
  --footer:#2b2b2b;
  --white:#fff;
}
*{box-sizing:border-box;margin:0;padding:0}
html,body{width:1200px;height:3919px;overflow:hidden}
body{font-family:"Roboto",Arial,sans-serif;color:var(--ink);background:var(--white);position:relative}
a{color:inherit;text-decoration:none}
.btn{display:inline-flex;align-items:center;gap:8px;border-radius:30px;font-weight:700;text-transform:uppercase;color:var(--white);background:var(--green)}
.btn svg{width:14px;height:14px}

/* header */
.site-header{position:absolute;top:0;left:0;width:1200px;height:65px;display:flex;align-items:center;background:var(--white)}
.brand{margin-left:42px;font-weight:700;font-size:19px;letter-spacing:.3px;color:var(--ink)}
.main-nav{display:flex;gap:26px;margin-left:82px;font-size:15px;font-weight:500}
.main-nav a{position:relative;padding:8px 0}
.main-nav a.active{color:var(--green);border-bottom:2px solid var(--green)}
.portal-btn{margin-left:auto;height:65px;width:222px;background:var(--green);color:var(--white);font-weight:700;font-size:15px;display:flex;align-items:center;justify-content:center;gap:8px;text-transform:uppercase}

/* hero */
.hero{position:absolute;top:65px;left:0;width:1200px;height:598px;background:linear-gradient(180deg,#6f8fb0 0%,#a9b7bf 35%,#6a7a4a 60%,#4b4f48 100%)}
.hero-photo{position:absolute;inset:0}
.hero-copy{position:absolute;left:110px;top:200px;color:var(--white)}
.hero-copy h1{font-size:45px;font-weight:700;letter-spacing:.5px}
.hero-copy p{font-size:16px;line-height:26px;width:470px;margin-top:10px;font-weight:500}
.hero-copy .btn{margin-top:28px;height:50px;padding:0 38px;font-size:16px}
.slider-arrow{position:absolute;top:260px;width:42px;height:42px;border:2px solid var(--white);border-radius:50%;display:flex;align-items:center;justify-content:center}
.slider-arrow.prev{left:31px}.slider-arrow.next{right:10px}

/* about */
.about{position:absolute;top:663px;left:0;width:1200px;height:472px;display:flex}
.about-photo{width:600px;height:100%;background:linear-gradient(180deg,#d9e6f0 0%,#b8cee0 45%,#c85b3d 55%,#2b4d8e 68%,#4b7da8 100%)}
.about-copy{width:600px;background:var(--blue);color:var(--white);padding:68px 60px}
.about-copy h2,.why-copy h2{font-size:38px;font-weight:700}
.about-copy p,.why-copy p{font-size:13.5px;line-height:25px;margin-top:22px;width:430px}
.about-copy p+p,.why-copy p+p{margin-top:12px}
.about-copy .btn,.why-copy .btn{margin-top:36px;height:48px;padding:0 31px;font-size:13.5px}

/* services */
.section-title{position:absolute;left:0;width:1200px;text-align:center;font-size:38px;font-weight:700;text-transform:uppercase}
.services{position:absolute;top:1310px;left:111px;width:978px;display:grid;grid-template-columns:repeat(3,316px);column-gap:15px;row-gap:38px}
.service{position:relative;height:348px}
.service-photo{height:234px}
.service-card{position:absolute;left:13px;right:13px;top:200px;height:148px;background:var(--white);box-shadow:0 3px 10px rgba(0,0,0,.12);text-align:center;padding-top:48px}
.service-icon{position:absolute;left:50%;top:-36px;margin-left:-38px;width:76px;height:76px;border-radius:50%;background:var(--white);display:flex;align-items:center;justify-content:center}
.service-icon svg{width:44px;height:44px;fill:none;stroke:var(--green);stroke-width:2}
.service-card h3{font-size:18.5px;font-weight:700}
.service-card p{font-size:13.5px;line-height:23px;color:var(--muted);margin:10px auto 0;width:260px}

/* why */
.why{position:absolute;top:2137px;left:0;width:1200px;height:472px;display:flex}
.why-copy{width:600px;background:var(--teal);color:var(--white);padding:66px 111px}
.why-photo{width:600px;background:linear-gradient(160deg,#5d6f86 0%,#c9b59a 35%,#f3c76a 55%,#6b6b66 75%,#3e4045 100%)}

/* resources */
.resources{position:absolute;top:2745px;left:111px;width:978px;display:flex;gap:26px}
.post{width:309px;height:388px;background:var(--white);box-shadow:0 3px 12px rgba(0,0,0,.12);border-radius:8px;padding:8px 8px 0;text-align:center}
.post-photo{height:204px;border-radius:4px}
.post-meta{margin-top:28px;font-size:13px;color:var(--blue);display:flex;justify-content:center;align-items:center;gap:8px}
.post-meta svg{width:12px;height:12px;fill:var(--blue)}
.post h3{font-size:16.5px;font-weight:500;margin-top:8px}
.post p{font-size:13.5px;line-height:22px;color:var(--muted);width:272px;margin:10px auto 0}
.post .read{display:inline-flex;align-items:center;gap:6px;margin-top:12px;font-size:14.5px;font-weight:500;color:var(--blue)}
.post .read svg{width:13px;height:13px}

/* cta */
.cta{position:absolute;top:3260px;left:0;width:1200px;height:298px;background:var(--green);color:var(--white);text-align:center}
.cta h2{margin-top:65px;font-size:35px;font-weight:700}
.cta p{font-size:14.5px;line-height:27px;width:940px;margin:14px auto 0}
.cta .btn{margin-top:28px;height:46px;padding:0 46px;font-size:14.5px;background:var(--blue)}

/* footer */
.site-footer{position:absolute;top:3558px;left:0;width:1200px;height:361px;background:var(--footer);color:#d7d7d7}
.footer-brand{position:absolute;left:166px;top:116px;font-weight:700;font-size:18.5px;color:var(--white)}
.socials{position:absolute;left:173px;top:148px;display:flex;gap:10px}
.socials span{width:30px;height:30px;border:1.5px solid #cfcfcf;border-radius:50%}
.footer-col{position:absolute;top:56px;font-size:13.5px}
.footer-col h4{font-size:16px;font-weight:500;color:var(--white);margin-bottom:18px}
.footer-col li{list-style:none;line-height:25.6px}
.col-links{left:444px}.col-company{left:645px}.col-contact{left:853px}
.contact-item{display:flex;gap:12px;margin-bottom:12px;line-height:20px}
.contact-item svg{width:14px;height:14px;fill:var(--blue);flex:none;margin-top:2px}
.contact-item strong{display:block;font-size:12px;font-weight:700;color:var(--white)}
.copyright{position:absolute;left:0;width:1200px;top:318px;text-align:center;font-size:14.5px}
.to-top{position:absolute;left:1107px;top:270px;width:34px;height:34px;border-radius:50%;background:var(--blue);display:flex;align-items:center;justify-content:center}
</style>
</head>
<body>

<header class="site-header">
  <a class="brand" href="#">FREIGHT BROKER</a>
  <nav class="main-nav">
    <a class="active" href="#">Home</a>
    <a href="#">About us</a>
    <a href="#">What We Do</a>
    <a href="#">We Specialize in</a>
    <a href="#">Customers</a>
    <a href="#">Carriers</a>
    <a href="#">Careers</a>
  </nav>
  <a class="portal-btn" href="#">
    <svg width="16" height="16" viewBox="0 0 16 16" fill="none" stroke="#fff" stroke-width="1.5"><circle cx="8" cy="8" r="7"/><circle cx="8" cy="6.3" r="2.3"/><path d="M3.5 12.8c1.2-1.8 2.7-2.5 4.5-2.5s3.3.7 4.5 2.5"/></svg>
    Customer Portal
  </a>
</header>

<section class="hero">
  <div class="hero-photo" role="img" aria-label="White semi-truck with trailer driving on a rural highway under a cloudy sky"></div>
  <a class="slider-arrow prev" href="#"><svg width="14" height="14" viewBox="0 0 14 14" fill="none" stroke="#fff" stroke-width="2"><path d="M9 2 4 7l5 5"/></svg></a>
  <a class="slider-arrow next" href="#"><svg width="14" height="14" viewBox="0 0 14 14" fill="none" stroke="#fff" stroke-width="2"><path d="m5 2 5 5-5 5"/></svg></a>
  <div class="hero-copy">
    <h1>FREIGHT BROKER</h1>
    <p>Lorem ipsum dolor sit amet, consectetur adipiscing elit, sed do eiusmod tempor incididunt ut labore aliqua.</p>
    <a class="btn" href="#">Get Started</a>
  </div>
</section>

<section class="about">
  <div class="about-photo" role="img" aria-label="Container cargo ship loaded with colourful containers at sea"></div>
  <div class="about-copy">
    <h2>ABOUT US</h2>
    <p>Sed ut perspiciatis unde omnis iste natus error sit voluptatem accusantium doloremque laudantium, totam rem aperiam, eaque ipsa quae ab illo inventore veritatis et quasi architecto beatae vitae dicta sunt explicabo.</p>
    <p>Nemo enim ipsam voluptatem quia voluptas sit aspernatur aut odit aut fugit, sed quia consequuntur magni dolores eos qui ratione voluptatem sequi nesciunt.</p>
    <a class="btn" href="#">Learn More <svg viewBox="0 0 14 14"><circle cx="7" cy="7" r="7" fill="#fff"/><path d="m6 4 3 3-3 3" fill="none" stroke="#8dc63f" stroke-width="1.8"/></svg></a>
  </div>
</section>

<h2 class="section-title" style="top:1220px">What We Do</h2>
<section class="services">
  <article class="service">
    <div class="service-photo" role="img" aria-label="Cargo ship docked at a container port with cranes" style="background:linear-gradient(180deg,#e8d9c8,#b5574a 55%,#3d5a78)"></div>
    <div class="service-card"><span class="service-icon"><svg viewBox="0 0 44 44"><circle cx="22" cy="22" r="16"/><path d="M6 22h32M22 6c-6 6-6 26 0 32M22 6c6 6 6 26 0 32"/></svg></span>
      <h3>Lorem ipsum dolor sit</h3><p>Lorem ipsum dolor sit amet, consectetur adipiscing elit, sed do aliqua.</p></div>
  </article>
  <article class="service">
    <div class="service-photo" role="img" aria-label="Airplane flying over stacked containers and trucks at sunset" style="background:linear-gradient(180deg,#8fa3b5,#f0c27a 50%,#6b5a4a)"></div>
    <div class="service-card"><span class="service-icon"><svg viewBox="0 0 44 44"><rect x="10" y="16" width="24" height="20"/><path d="M10 22h24M18 16v6M26 16v6M16 10h12"/></svg></span>
      <h3>Lorem ipsum dolor sit</h3><p>Lorem ipsum dolor sit amet, consectetur adipiscing elit, sed do aliqua.</p></div>
  </article>
  <article class="service">
    <div class="service-photo" role="img" aria-label="Worker in safety vest in a container yard" style="background:linear-gradient(180deg,#3e5c9a,#4a6fb0 50%,#9a4f4a)"></div>
    <div class="service-card"><span class="service-icon"><svg viewBox="0 0 44 44"><circle cx="18" cy="22" r="12"/><path d="M6 22h24M18 10v24"/><rect x="26" y="14" width="12" height="16"/></svg></span>
      <h3>Lorem ipsum dolor sit</h3><p>Lorem ipsum dolor sit amet, consectetur adipiscing elit, sed do aliqua.</p></div>
  </article>
  <article class="service">
    <div class="service-photo" role="img" aria-label="Plane above a port with stacked containers and cranes" style="background:linear-gradient(180deg,#a9c7e0,#5e8aa8 45%,#3f7a4f 75%,#3c6f93)"></div>
    <div class="service-card"><span class="service-icon"><svg viewBox="0 0 44 44"><path d="M8 14l22-4 4 4-22 4z"/><rect x="10" y="22" width="24" height="14"/><path d="M16 22v14M22 22v14M28 22v14"/></svg></span>
      <h3>Lorem ipsum dolor sit</h3><p>Lorem ipsum dolor sit amet, consectetur adipiscing elit, sed do aliqua.</p></div>
  </article>
  <article class="service">
    <div class="service-photo" role="img" aria-label="Truck on a dusty country road at sunset" style="background:linear-gradient(180deg,#9aa5ad,#e9c48a 45%,#b7a37a 75%,#8a7c5e)"></div>
    <div class="service-card"><span class="service-icon"><svg viewBox="0 0 44 44"><rect x="12" y="8" width="20" height="28" rx="2"/><circle cx="22" cy="20" r="5"/><path d="M16 30h12"/></svg></span>
      <h3>Lorem ipsum dolor sit</h3><p>Lorem ipsum dolor sit amet, consectetur adipiscing elit, sed do aliqua.</p></div>
  </article>
  <article class="service">
    <div class="service-photo" role="img" aria-label="Two trucks on a highway through green trees" style="background:linear-gradient(180deg,#7fa1c7,#c3d6e3 35%,#5d7d3e 60%,#6b7278)"></div>
    <div class="service-card"><span class="service-icon"><svg viewBox="0 0 44 44"><rect x="12" y="8" width="16" height="28" rx="3"/><circle cx="28" cy="16" r="6"/><path d="M17 31h6"/></svg></span>
      <h3>Lorem ipsum dolor sit</h3><p>Lorem ipsum dolor sit amet, consectetur adipiscing elit, sed do aliqua.</p></div>
  </article>
</section>

<section class="why">
  <div class="why-copy">
    <h2>WHY CHOOSE US?</h2>
    <p>Sed ut perspiciatis unde omnis iste natus error sit voluptatem accusantium doloremque laudantium, totam rem aperiam, eaque ipsa quae ab illo inventore veritatis et quasi architecto beatae vitae dicta sunt explicabo.</p>
    <p>Nemo enim ipsam voluptatem quia voluptas sit aspernatur aut odit aut fugit, sed quia consequuntur magni dolores eos qui ratione voluptatem sequi nesciunt.</p>
    <a class="btn" href="#">Learn More <svg viewBox="0 0 14 14"><circle cx="7" cy="7" r="7" fill="#fff"/><path d="m6 4 3 3-3 3" fill="none" stroke="#8dc63f" stroke-width="1.8"/></svg></a>
  </div>
  <div class="why-photo" role="img" aria-label="Semi-truck on a highway with the sun setting behind"></div>
</section>

<h2 class="section-title" style="top:2668px">Our Resources</h2>
<section class="resources">
  <article class="post">
    <div class="post-photo" role="img" aria-label="Cargo plane over trucks and a ship at a sunset port" style="background:linear-gradient(180deg,#8b9cb0,#f2b872 50%,#6c4a3a)"></div>
    <div class="post-meta"><svg viewBox="0 0 12 12"><path d="M1 3h10v8H1zM3 1h1v2H3zM8 1h1v2H8z"/></svg>June 25, 2021 &nbsp;|&nbsp; By Marlow</div>
    <h3>Lorem ipsum dolor sit consectetur</h3>
    <p>Sed ut perspiciatis unde omnis iste natus error sit voluptatem accusantium</p>
    <a class="read" href="#">READ MORE <svg viewBox="0 0 14 14"><circle cx="7" cy="7" r="7" fill="#2f74b8"/><path d="m6 4 3 3-3 3" fill="none" stroke="#fff" stroke-width="1.8"/></svg></a>
  </article>
  <article class="post">
    <div class="post-photo" role="img" aria-label="Aerial view of a rail yard full of freight wagons" style="background:linear-gradient(160deg,#3f7d88,#9a5e4c 50%,#2f6a7e)"></div>
    <div class="post-meta"><svg viewBox="0 0 12 12"><path d="M1 3h10v8H1zM3 1h1v2H3zM8 1h1v2H8z"/></svg>June 25, 2021 &nbsp;|&nbsp; By Marlow</div>
    <h3>Lorem ipsum dolor sit consectetur</h3>
    <p>Sed ut perspiciatis unde omnis iste natus error sit voluptatem accusantium</p>
    <a class="read" href="#">READ MORE <svg viewBox="0 0 14 14"><circle cx="7" cy="7" r="7" fill="#2f74b8"/><path d="m6 4 3 3-3 3" fill="none" stroke="#fff" stroke-width="1.8"/></svg></a>
  </article>
  <article class="post">
    <div class="post-photo" role="img" aria-label="Warehouse office desk with a laptop among stacked boxes" style="background:linear-gradient(180deg,#e9e6e2,#cdb9a1 60%,#a58d74)"></div>
    <div class="post-meta"><svg viewBox="0 0 12 12"><path d="M1 3h10v8H1zM3 1h1v2H3zM8 1h1v2H8z"/></svg>June 25, 2021 &nbsp;|&nbsp; By Marlow</div>
    <h3>Lorem ipsum dolor sit consectetur</h3>
    <p>Sed ut perspiciatis unde omnis iste natus error sit voluptatem accusantium</p>
    <a class="read" href="#">READ MORE <svg viewBox="0 0 14 14"><circle cx="7" cy="7" r="7" fill="#2f74b8"/><path d="m6 4 3 3-3 3" fill="none" stroke="#fff" stroke-width="1.8"/></svg></a>
  </article>
</section>

<section class="cta">
  <h2>ARE YOU READY TO “FREIGHT BROKER” ?</h2>
  <p>Lorem ipsum dolor sit amet, consectetur adipiscing elit, sed do eiusmod tempor incididunt ut labore et dolore magna aliqua. Ut enim ad minim veniam, quis nostrud exercitation ullamco laboris nisi ut aliquip ex</p>
  <a class="btn" href="#">Contact Us <svg viewBox="0 0 14 14"><circle cx="7" cy="7" r="7" fill="#fff"/><path d="m6 4 3 3-3 3" fill="none" stroke="#2f74b8" stroke-width="1.8"/></svg></a>
</section>

<footer class="site-footer">
  <div class="footer-brand">FREIGHT BROKER</div>
  <div class="socials"><span></span><span></span><span></span><span></span></div>
  <div class="footer-col col-links">
    <h4>Quick Links</h4>
    <ul><li>Home</li><li>About us</li><li>What We Do</li><li>We Specialize in</li><li>Customers</li><li>Carriers</li></ul>
  </div>
  <div class="footer-col col-company">
    <h4>About Company</h4>
    <ul><li>Legal Information</li><li>Terms &amp; Condition</li><li>Privacy Policy</li><li>Site Map</li><li>FAQ</li></ul>
  </div>
  <div class="footer-col col-contact">
    <h4>Contact Us</h4>
    <div class="contact-item"><svg viewBox="0 0 14 14"><path d="M3 1l2 3-1.3 1.5a8 8 0 0 0 4.8 4.8L10 9l3 2-1 2C6 13 1 8 1 2z"/></svg><div><strong>Phone</strong>555.014.2287</div></div>
    <div class="contact-item"><svg viewBox="0 0 14 14"><path d="M1 3h12v8H1z"/><path d="m1 3 6 5 6-5" fill="none" stroke="#2b2b2b" stroke-width="1"/></svg><div><strong>Email</strong>info@freightbroker-desk.net</div></div>
    <div class="contact-item"><svg viewBox="0 0 14 14"><path d="M7 1a4.5 4.5 0 0 1 4.5 4.5C11.5 9 7 13 7 13S2.5 9 2.5 5.5A4.5 4.5 0 0 1 7 1z"/><circle cx="7" cy="5.5" r="1.6" fill="#2b2b2b"/></svg><div><strong>Location</strong>4410 Harlow Ridge Rd. Suite 118,<br>Cedar Hollow, Tx. 77590</div></div>
  </div>
  <a class="to-top" href="#"><svg width="14" height="14" viewBox="0 0 14 14" fill="none" stroke="#fff" stroke-width="2"><path d="m3 9 4-4 4 4"/></svg></a>
  <div class="copyright">2021 Copyright - Freight Broker | All Rights Reserved</div>
</footer>

</body>
</html>
```